I am a home builder and developer

I would like some sort of architectural design like a pencil type of drawing of a house but want it to be professional looking and two sided.

Simply I am a custom home builder and land developer. I would like a new design other than what I have now that's what I thought y'all did. I like mostly black maybe with an pencil type of drawing of a house. Like an architectural look.

Industry/Entity Type

Home Builder

```html
<!DOCTYPE html>
<html lang="en">
<head>
<meta charset="utf-8">
<title>R &amp; K Homes Inc — Business Card</title>
<link rel="stylesheet" href="https://fonts.googleapis.com/css2?family=Montserrat:wght@400;500;600&display=swap">
<style>
  :root {
    --backdrop: #4a3f39;
    --card: #111111;
    --card-edge: #1c1c1c;
    --emboss: #181818;
    --emboss-edge: #202020;
    --ink: #f2f2f2;
    --ink-soft: #bdbdbd;
    --rule: #e6e6e6;
  }
  * { margin: 0; padding: 0; box-sizing: border-box; }
  html, body {
    width: 1200px;
    height: 716px;
    overflow: hidden;
    background: var(--backdrop);
    font-family: "Montserrat", Arial, sans-serif;
  }
  .stage {
    width: 1200px;
    height: 716px;
    display: flex;
    align-items: center;
    justify-content: center;
    gap: 40px;
  }
  .card {
    position: relative;
    width: 540px;
    height: 309px;
    background: var(--card);
    border: 1px solid var(--card-edge);
    border-radius: 3px;
    box-shadow: 0 10px 24px rgba(0, 0, 0, 0.35);
    overflow: hidden;
  }

  /* Front */
  .card-front .company-name {
    position: absolute;
    left: 40px;
    top: 56px;
    font-size: 19px;
    font-weight: 500;
    letter-spacing: 0.3px;
    color: var(--ink-soft);
  }
  .card-front .emboss-motif {
    position: absolute;
    left: 130px;
    top: 92px;
    width: 370px;
    height: 196px;
    background: var(--emboss);
    border: 1px solid var(--emboss-edge);
  }

  /* Back */
  .card-back .rules {
    position: absolute;
    inset: 0;
  }
  .card-back .brand {
    position: absolute;
    right: 40px;
    top: 72px;
    display: flex;
    flex-direction: column;
    align-items: flex-end;
    gap: 24px;
  }
  .card-back .brand-square {
    width: 58px;
    height: 58px;
    border: 1.5px solid var(--rule);
    margin-right: 50px;
  }
  .card-back .company-name {
    font-size: 17px;
    font-weight: 600;
    letter-spacing: 0.3px;
    color: var(--ink);
  }
  .card-back .contact {
    position: absolute;
    left: 40px;
    top: 138px;
    color: var(--ink);
    font-size: 13.5px;
    font-weight: 400;
    line-height: 23px;
    letter-spacing: 0.2px;
  }
  .card-back .person-name {
    text-transform: uppercase;
    letter-spacing: 0.8px;
  }
</style>
</head>
<body>
  <main class="stage">
    <section class="card card-front" aria-label="Card front">
      <p class="company-name">R &amp; K Homes Inc</p>
      <div class="emboss-motif" role="img" aria-label="Blind-embossed architectural line drawing of a house and tall buildings"></div>
    </section>

    <section class="card card-back" aria-label="Card back">
      <svg class="rules" width="540" height="309" viewBox="0 0 540 309" aria-hidden="true">
        <line x1="160" y1="152" x2="500" y2="152" stroke="var(--rule)" stroke-width="1"/>
        <line x1="40" y1="256" x2="500" y2="256" stroke="var(--rule)" stroke-width="1"/>
      </svg>
      <div class="brand">
        <span class="brand-square" aria-hidden="true"></span>
        <p class="company-name">R &amp; K Homes Inc</p>
      </div>
      <div class="contact">
        <p class="person-name">Daniel Reyes</p>
        <p class="phone">T: 555-014-2287</p>
        <p class="email">E: hello@rkhomesinc.com</p>
      </div>
    </section>
  </main>
</body>
</html>
```